Stationery Design Task - Stationary, memo and report templates for professional services company

Looking for someone to update stationary design but just as importantly come up with a template for reports and memos for use in our consulting firm. Would also like some brand use guidelines to be able to share with our whole team. We have an existing logo that we like. Need to update with a more contemporary look so that our deliverables to clients look good and professional yet stylish. This is for business to business communications. No need for envelope design. Important to have design for multiple pages, i.e. first page of a report and then 2nd page. Need to use in MS word documents so must be easy to use and replicate. Don't want something overly complex. Clean, fresh looking is best.

Industry/Entity Type

Information Technology

Font styles to use
Sans Serif

Colors
33a6d7
0792cd
85cae6
cee9f5
cedeed
85abd2
3377b5
0455a3

Requirements
Must have
• Clean look but with a little style or pop. Something that can easily be used in word documents. Need to have page styles that have a first page of a report (not a cover page) and then secondary page.
Nice to have
• - Although the dark blue is our primary color. Might be willing to look at some accent color as well.
Should not have
• Not just our logo on the page with a color bar.

```html
<!DOCTYPE html>
<html lang="en">
<head>
<meta charset="utf-8">
<title>Nimbus Systems – Report and Letter Templates</title>
<link href="https://fonts.googleapis.com/css2?family=Roboto:wght@400;700;900&family=Questrial&display=swap" rel="stylesheet">
<style>
  :root {
    --stage: #6b6b6b;
    --paper: #ffffff;
    --brand-blue: #0a80c9;
    --deep-blue: #0455a3;
    --mid-blue: #0792cd;
    --sky-blue: #33a6d7;
    --pale-blue: #85cae6;
    --divider: #d9dde2;
    --ink: #4a4a4a;
    --ink-soft: #6a6a6a;
    --white: #ffffff;
  }
  * { margin: 0; padding: 0; box-sizing: border-box; }
  html, body { width: 1200px; height: 578px; overflow: hidden; }
  body {
    background: var(--stage);
    position: relative;
    font-family: "Questrial", "Century Gothic", sans-serif;
  }
  .page {
    position: absolute;
    top: 53px;
    width: 338px;
    height: 475px;
    background: var(--paper);
    box-shadow: 0 0 4px rgba(0,0,0,.35);
    overflow: hidden;
  }
  .page--cover { left: 62px; }
  .page--letter { left: 434px; }
  .page--continuation { left: 806px; background: linear-gradient(90deg, #dcdcdc 0%, #f1f1f1 45%, #fafafa 100%); }
  .page-frame {
    position: absolute;
    left: 7px; top: 7px; right: 7px; bottom: 7px;
    border: 1px solid var(--deep-blue);
    pointer-events: none;
  }

  /* Brand name */
  .brand { position: absolute; display: flex; align-items: center; }
  .brand-dot { border-radius: 50%; background: var(--brand-blue); flex: none; }
  .brand-name {
    font-family: "Roboto", Arial, sans-serif;
    font-weight: 900;
    color: var(--brand-blue);
    line-height: .95;
    letter-spacing: -.2px;
  }
  .page--cover .brand { left: 0; right: 0; top: 50px; justify-content: center; gap: 10px; }
  .page--cover .brand-dot { width: 38px; height: 38px; }
  .page--cover .brand-name { font-size: 27px; }
  .page--letter .brand { left: 28px; top: 34px; gap: 6px; }
  .page--letter .brand-dot { width: 26px; height: 26px; }
  .page--letter .brand-name { font-size: 15px; }

  /* Cover */
  .cover-art { position: absolute; left: 0; top: 0; width: 338px; height: 475px; }
  .cover-title {
    position: absolute; left: 0; right: 0; top: 218px;
    text-align: center; color: var(--white);
    font-family: "Roboto", Arial, sans-serif;
  }
  .cover-title h1 { font-size: 31px; font-weight: 900; line-height: 1.03; letter-spacing: .2px; }
  .cover-title p { font-size: 12px; font-weight: 700; margin-top: 4px; }
  .cover-date {
    position: absolute; top: 362px; width: 60px;
    text-align: center; color: var(--white);
    font-family: "Roboto", Arial, sans-serif;
    font-size: 8.5px; line-height: 1.15;
  }
  .cover-date--issued { left: 15px; }
  .cover-date--valid { left: 263px; }
  .cover-author {
    position: absolute; left: 0; right: 0; top: 416px;
    text-align: center; color: var(--white);
    font-family: "Roboto", Arial, sans-serif;
  }
  .cover-author strong { display: block; font-size: 12px; font-weight: 900; letter-spacing: .3px; }
  .cover-author span { display: block; font-size: 10.5px; margin-top: 2px; }

  /* Letter */
  .contact-bar {
    position: absolute; left: 163px; top: 32px; width: 168px; height: 34px;
    background: var(--brand-blue); color: var(--white);
    padding: 10px 0 0 8px;
    font-family: "Roboto", Arial, sans-serif;
    font-size: 5.6px; font-weight: 700; line-height: 1.45; letter-spacing: .1px;
  }
  .watermark {
    position: absolute;
    background: radial-gradient(circle, rgba(200,200,200,.35) 0%, rgba(220,220,220,.18) 50%, rgba(255,255,255,0) 72%);
  }
  .page--letter .watermark { left: 90px; top: 110px; width: 250px; height: 300px; }
  .page--continuation .watermark { left: 60px; top: 80px; width: 280px; height: 330px; background: radial-gradient(circle, rgba(255,255,255,.55) 0%, rgba(255,255,255,.2) 50%, rgba(255,255,255,0) 72%); }
  .letter-body {
    position: absolute; left: 30px; top: 136px; width: 284px;
    color: var(--ink);
  }
  .salutation { font-size: 9px; margin-bottom: 10px; }
  .letter-body p.copy {
    font-size: 4.9px; line-height: 8.4px; text-align: justify; margin-bottom: 7px;
    color: var(--ink-soft);
  }
  .closing { font-size: 5px; color: var(--ink-soft); margin-top: 10px; }
  .signature {
    width: 60px; height: 26px; margin-top: 6px;
    background: linear-gradient(90deg, rgba(120,140,190,.18), rgba(120,140,190,.05));
    border-radius: 3px;
  }
  .site-url {
    position: absolute; left: 0; right: 0; top: 447px;
    text-align: center; color: var(--brand-blue);
    font-family: "Roboto", Arial, sans-serif;
    font-size: 5.8px; letter-spacing: 1.6px;
  }
</style>
</head>
<body>

  <!-- Report first page -->
  <section class="page page--cover">
    <svg class="cover-art" viewBox="0 0 338 475" aria-hidden="true">
      <defs>
        <linearGradient id="cover-sky" x1="0" y1="0" x2="0" y2="1">
          <stop offset="0" stop-color="#ffffff"/>
          <stop offset="1" stop-color="#eeeff0"/>
        </linearGradient>
        <linearGradient id="cover-blue" x1="0" y1="0" x2="0.4" y2="1">
          <stop offset="0" stop-color="#0b7ec6"/>
          <stop offset="1" stop-color="#0458a0"/>
        </linearGradient>
      </defs>
      <rect x="7" y="7" width="324" height="131" fill="url(#cover-sky)"/>
      <rect x="7" y="138" width="324" height="330" fill="url(#cover-blue)"/>
      <polygon points="7,150 18,138 44,138 30,172 7,198" fill="#2a9ad6"/>
      <polygon points="331,150 320,138 294,138 308,172 331,198" fill="#2a9ad6"/>
      <g fill="none" stroke="#d9dde2" stroke-width="3" stroke-linejoin="miter">
        <polygon points="58,138 280,138 316,259 242,385 96,385 22,259"/>
        <line x1="96" y1="385" x2="46" y2="468"/>
        <line x1="242" y1="385" x2="292" y2="468"/>
        <line x1="30" y1="172" x2="7" y2="198"/>
        <line x1="308" y1="172" x2="331" y2="198"/>
        <line x1="22" y1="259" x2="7" y2="236"/>
        <line x1="316" y1="259" x2="331" y2="236"/>
      </g>
    </svg>

    <div class="brand">
      <span class="brand-dot"></span>
      <span class="brand-name">NIMBUS SYSTEMS</span>
    </div>

    <div class="cover-title">
      <h1>REPORT<br>TITLE HERE</h1>
      <p>YOUR SUBTITLE HERE</p>
    </div>

    <div class="cover-date cover-date--issued">PROPOSAL<br>ISSUED<br>SEP 19,2018</div>
    <div class="cover-date cover-date--valid">PROPOSAL<br>VALID TO<br>SEP 19,2019</div>

    <div class="cover-author">
      <strong>REPORT PREPARED BY</strong>
      <span>YOUR NAME HERE</span>
    </div>

    <div class="page-frame"></div>
  </section>

  <!-- Letterhead -->
  <section class="page page--letter">
    <div class="watermark" role="img" aria-label="Faint brand decoration behind the letter text"></div>

    <div class="brand">
      <span class="brand-dot"></span>
      <span class="brand-name">NIMBUS<br>SYSTEMS</span>
    </div>
    <div class="contact-bar">
      2140 HARBOR VIEW ROAD, PORTLAND, OREGON 97205<br>
      503 555 0147 | HELLO@NIMBUSSYSTEMS.COM
    </div>

    <div class="letter-body">
      <p class="salutation">Dear Mr. Carter,</p>
      <p class="copy">Thank you for the opportunity to review your current network and support arrangements. Our team has completed the initial assessment and we are pleased to share a summary of the findings. The enclosed notes outline the systems we examined, the main risks we identified and the areas where modest changes could bring clear gains in stability and cost.</p>
      <p class="copy">We recommend a phased approach that begins with a review of backup routines and user access, followed by an upgrade of the core servers later in the year. Each phase has been planned to keep disruption to a minimum, and our consultants will work alongside your staff so that knowledge stays within your organisation.</p>
      <p class="copy">A detailed schedule, budget estimate and list of deliverables are attached for your consideration. We have also included a short comparison of hosting options, as several of your teams asked about moving selected services to the cloud. Should you wish to discuss any part of the proposal, we would be glad to arrange a meeting at a time that suits you and your colleagues in the coming weeks.</p>
      <p class="copy">We appreciate the trust you have placed in our firm and look forward to supporting your business as it grows. Please contact our office if you have any questions about this letter or the attached documents.</p>
      <p class="closing">Sincerely,</p>
      <div class="signature" role="img" aria-label="Handwritten signature"></div>
    </div>

    <div class="site-url">WWW.NIMBUSSYSTEMS.COM</div>
    <div class="page-frame"></div>
  </section>

  <!-- Continuation page -->
  <section class="page page--continuation">
    <div class="watermark" role="img" aria-label="Faint brand decoration in the page background"></div>
    <div class="site-url">WWW.NIMBUSSYSTEMS.COM</div>
    <div class="page-frame"></div>
  </section>

</body>
</html>
```